Company Business Card (Company Promotions)

We want a Business Card that is both Elegant & High Class. We want the card stock thick and unique. We want it to build our Brand Name. We service Automobile dealerships & owners who drive luxury & exotic automobiles that cost an average of $75K. We provide towing services for Luxury & Exotic vehicles. Our colors are Black & Construction Yellow (Gold).
We are manufacture certified for Valdora Kent, RQT, PUKA, ELVO, Tavrine, HJ, Colvesi, Pendrel, Casteduvro, Ombra & Sorvanel. We have authorization to use their logo's.
Enclosed is our old business card. We only used the unusual & Unique brands on the cards but are open to the use of all of them. We also use the Federal Competence Badge that identifies our abilities.

Also enclosed is the name font that we use.

Target Market(s)

Business, Executive, Hi end people that drive finer luxury &/or exotic automobiles.

Industry/Entity Type

Business

Contact Information for Business Card

We market our name. Haul Crestmark. Business address is: 4812 Willowmere Lane, NE Ste: 210, Atlanta, GA 30399 Phone: 404-555-0148. Web address is crestmarkhaul-example.com
Manufacture Certified / Nationally Certified

Font styles to use
Other font styles liked:
• AR DESTINE (in Italic's)

Colors
ffc214

Requirements
Must have
• Must have the at least 5 of the manufacture logo's and the Guild Council Emblem (see on other business card)
Nice to have
• Place the manfacture logo's on the back.
Should not have
• No other colors than Black, Yellow & White

```html
<!DOCTYPE html>
<html lang="en">
<head>
<meta charset="utf-8">
<title>Haul Crestmark – Business Card</title>
<link href="https://fonts.googleapis.com/css2?family=Russo+One&family=Roboto+Slab:wght@700&display=swap" rel="stylesheet">
<style>
  :root{
    --bg:#d9d6d0;
    --black:#0c0c0c;
    --carbon:#1b1b1b;
    --steel-a:#3a3a3a;
    --steel-b:#1e1e1e;
    --yellow:#ffc214;
    --yellow-soft:#ffe08a;
    --white:#f4f4f4;
    --strip-edge:#cfcfcf;
  }
  *{box-sizing:border-box;margin:0;padding:0}
  html,body{width:1200px;height:892px;overflow:hidden;background:var(--bg)}
  .canvas{position:relative;width:1200px;height:892px}
  .card{position:absolute;width:640px;height:366px;border-radius:22px;overflow:hidden;background:var(--black);box-shadow:0 6px 18px rgba(0,0,0,.25)}
  .card-front{left:70px;top:60px}
  .card-back{left:490px;top:466px}

  /* front */
  .carbon{position:absolute;inset:0;background:
      radial-gradient(circle at 2px 2px,#2c2c2c 1.2px,transparent 1.6px) 0 0/5px 5px,
      var(--carbon)}
  .steel-wave{position:absolute;inset:0}
  .brand-strip{position:absolute;right:0;top:0;width:84px;height:100%;
      background:linear-gradient(90deg,var(--strip-edge),var(--white) 30%);
      display:flex;flex-direction:column;justify-content:space-between;align-items:center;padding:14px 4px}
  .maker{font-family:"Roboto Slab",serif;font-weight:700;font-size:10px;color:var(--black);letter-spacing:.2px;text-align:center;line-height:1}
  .wordmark{position:absolute;left:150px;top:34px;font-family:"Russo One",sans-serif;font-weight:400;font-size:46px;color:var(--yellow);letter-spacing:1px;line-height:1;white-space:nowrap}
  .tagline{position:absolute;left:110px;top:92px;font-family:"Roboto Slab",serif;font-weight:700;font-size:15px;color:var(--yellow);white-space:nowrap}
  .contact{position:absolute;right:104px;top:150px;list-style:none;text-align:right;
      font-family:"Roboto Slab",serif;font-weight:700;font-size:17px;color:var(--yellow);line-height:27px;white-space:nowrap}
  .contact li{display:flex;justify-content:flex-end;align-items:center;gap:10px}
  .contact svg{width:14px;height:14px;flex:none}
  .contact .address{display:block;line-height:22px;margin-top:2px}
  .badge{position:absolute;left:34px;top:222px;width:110px;height:120px}

  /* back */
  .gloss{position:absolute;inset:0;background:linear-gradient(160deg,#1d1d1d 0%,var(--black) 45%,#151515 100%)}
  .badge-faint{position:absolute;left:150px;top:70px;width:200px;height:220px;opacity:.22}
  .back-wordmark{position:absolute;left:0;right:0;top:150px;text-align:center;font-family:"Russo One",sans-serif;font-weight:400;font-size:52px;color:var(--yellow);letter-spacing:1px;white-space:nowrap}
  .rule{position:absolute;left:70px;right:70px;top:228px;height:2px;background:var(--yellow)}
</style>
</head>
<body>
<main class="canvas">

  <section class="card card-front" aria-label="Business card front">
    <div class="carbon"></div>
    <svg class="steel-wave" viewBox="0 0 640 366" preserveAspectRatio="none" aria-hidden="true">
      <defs>
        <linearGradient id="steel" x1="0" y1="0" x2="0" y2="1">
          <stop offset="0" stop-color="#3a3a3a"/>
          <stop offset="1" stop-color="#1e1e1e"/>
        </linearGradient>
      </defs>
      <path d="M0 130 C70 130 110 170 150 230 C185 290 215 330 250 366 L0 366 Z" fill="url(#steel)"/>
      <path d="M0 130 C70 130 110 170 150 230 C185 290 215 330 250 366" fill="none" stroke="#000" stroke-opacity=".5" stroke-width="2"/>
    </svg>

    <aside class="brand-strip" aria-label="Certified manufacturers">
      <span class="maker">Brackwell</span>
      <span class="maker">Sablet</span>
      <span class="maker">Tridona</span>
      <span class="maker">Tavrine</span>
      <span class="maker">Ironvale</span>
      <span class="maker">Valdora<br>Kent</span>
      <span class="maker">Morvane</span>
      <span class="maker">ELVO</span>
      <span class="maker">RQT</span>
    </aside>

    <h1 class="wordmark">Haul Crestmark</h1>
    <p class="tagline">Manufacture Certified / Nationally Certified</p>

    <ul class="contact">
      <li>404-555-0148
        <svg viewBox="0 0 14 14" aria-hidden="true"><rect width="14" height="14" rx="2" fill="var(--yellow)"/><path d="M4 3l2 2-1 1.2c.6 1.3 1.5 2.2 2.8 2.8L9 8l2 2-1.3 1.3C6.5 11 3 7.5 2.7 4.3Z" fill="#000"/></svg></li>
      <li>404-555-0192
        <svg viewBox="0 0 14 14" aria-hidden="true"><rect width="14" height="14" rx="2" fill="var(--yellow)"/><rect x="4" y="2.5" width="6" height="9" rx="1" fill="#000"/></svg></li>
      <li>www.crestmarkhaul-example.com
        <svg viewBox="0 0 14 14" aria-hidden="true"><rect width="14" height="14" rx="2" fill="var(--yellow)"/><circle cx="7" cy="7" r="4" fill="none" stroke="#000" stroke-width="1.4"/><path d="M3 7h8M7 3v8" stroke="#000" stroke-width="1"/></svg></li>
      <li>4812 Willowmere Lane, NE Ste:
        <svg viewBox="0 0 14 14" aria-hidden="true"><rect width="14" height="14" rx="2" fill="var(--yellow)"/><path d="M7 12s-3.5-4-3.5-6.3a3.5 3.5 0 0 1 7 0C10.5 8 7 12 7 12Z" fill="#000"/></svg></li>
      <li class="address">210, Atlanta, GA 30399</li>
    </ul>

    <svg class="badge" viewBox="0 0 110 120" role="img" aria-label="Federal Competence Badge">
      <defs>
        <linearGradient id="badgeTone" x1="0" y1="0" x2="0" y2="1">
          <stop offset="0" stop-color="#f4f4f4"/>
          <stop offset="1" stop-color="#ffe08a"/>
        </linearGradient>
      </defs>
      <path d="M55 4 L104 16 C104 70 86 100 55 116 C24 100 6 70 6 16 Z" fill="url(#badgeTone)" stroke="var(--yellow)" stroke-width="5"/>
    </svg>
  </section>

  <section class="card card-back" aria-label="Business card back">
    <div class="gloss"></div>
    <svg class="badge-faint" viewBox="0 0 110 120" role="img" aria-label="Federal Competence Badge, faint">
      <path d="M55 4 L104 16 C104 70 86 100 55 116 C24 100 6 70 6 16 Z" fill="#f4f4f4"/>
    </svg>
    <h2 class="back-wordmark">Haul Crestmark</h2>
    <div class="rule"></div>
  </section>

</main>
</body>
</html>
```